Meridale Bed Company Needs Business Card

Looking for a very nice looking business card. Creative but not extravagant. We sell beds and pillows across the U.S. and need something professional but catchy. I have attached the logo.

Name : Devin Holt
Title : President
Phone : (800) 471-2960
Email: sleep@quilmora.com
Website: www.quilmora.com

Can be single-sided or double-sided
horizontal or vertical

Can use Blues/Greys

Target Market(s)

Mass Market

Industry/Entity Type

Retail

Contact Information for Business Card

Name : Devin Holt
Title : President
Phone : (800) 471-2960
Email: sleep@quilmora.com
Website: www.quilmora.com

Requirements
Must have
• Clean, Modern, Smooth
• Can use Blues/Greys
• On the other side without the information - have something simple like www.quilmora.com or our logo
Nice to have
• Surprise me
Should not have
• Nothing crazy, nothing cluttered

```html
<!DOCTYPE html>
<html lang="en">
<head>
<meta charset="utf-8">
<title>Meridale Bed Company – Business Card</title>
<link rel="stylesheet" href="https://fonts.googleapis.com/css2?family=Quicksand:wght@300&family=Arimo:wght@400;700&display=swap">
<style>
  :root {
    --stage: #3a3330;
    --card-blue: #6aafcb;
    --card-grey: #abacac;
    --mark-on-blue: #9fe9f4;
    --accent: #2ba3dd;
    --ink: #3b3d40;
    --ink-dark: #1f2124;
    --divider: #f2f2f2;
  }
  * { margin: 0; padding: 0; box-sizing: border-box; }
  html, body { width: 1200px; height: 769px; overflow: hidden; }
  body {
    background: var(--stage);
    position: relative;
    font-family: "Arimo", Arial, sans-serif;
  }
  .card {
    position: absolute;
    width: 520px;
    height: 297px;
    border-radius: 3px;
    box-shadow: 0 10px 24px rgba(0,0,0,0.45);
  }
  .card--front {
    left: 70px; top: 90px;
    background: var(--card-blue);
    display: flex; align-items: center; justify-content: center;
  }
  .card--back {
    left: 610px; top: 382px;
    background: var(--card-grey);
  }
  .wordmark {
    font-family: "Quicksand", "Century Gothic", sans-serif;
    font-weight: 300;
    letter-spacing: 2px;
    line-height: 1;
  }
  .card--front .wordmark {
    font-size: 92px;
    color: var(--mark-on-blue);
  }
  .card--back .wordmark {
    position: absolute;
    left: 150px; top: 52px;
    font-size: 86px;
    color: var(--accent);
  }
  .holder {
    position: absolute;
    right: 290px; top: 190px;
    text-align: right;
  }
  .holder__name {
    font-weight: 700;
    font-size: 19px;
    color: var(--accent);
  }
  .holder__title {
    font-size: 17px;
    color: var(--ink-dark);
    margin-top: 2px;
  }
  .divider {
    position: absolute;
    left: 244px; top: 186px;
    width: 1.5px; height: 74px;
    background: var(--divider);
  }
  .contact {
    position: absolute;
    left: 262px; top: 190px;
    list-style: none;
  }
  .contact__item {
    display: flex; align-items: center; gap: 8px;
    font-size: 15px;
    color: var(--ink);
    height: 22px;
  }
  .contact__icon { width: 14px; height: 14px; flex: none; }
</style>
</head>
<body>
  <section class="card card--front" aria-label="Card front">
    <span class="wordmark">quilmora</span>
  </section>

  <section class="card card--back" aria-label="Card back">
    <span class="wordmark">quilmora</span>

    <div class="holder">
      <p class="holder__name">Devin Holt</p>
      <p class="holder__title">President</p>
    </div>

    <span class="divider"></span>

    <ul class="contact">
      <li class="contact__item">
        <svg class="contact__icon" viewBox="0 0 14 14" aria-hidden="true">
          <path d="M1 4 Q7 0 13 4 L11 6 L9 5 L9 4 Q7 3 5 4 L5 5 L3 6 Z" fill="var(--accent)"/>
          <rect x="3" y="7" width="8" height="6" rx="1" fill="var(--accent)"/>
        </svg>
        (800) 471-2960
      </li>
      <li class="contact__item">
        <svg class="contact__icon" viewBox="0 0 14 14" aria-hidden="true">
          <rect x="1" y="3" width="12" height="9" rx="1" fill="var(--accent)"/>
          <path d="M1.5 3.5 L7 8 L12.5 3.5" fill="none" stroke="var(--card-grey)" stroke-width="1.2"/>
        </svg>
        sleep@quilmora.com
      </li>
      <li class="contact__item">
        <svg class="contact__icon" viewBox="0 0 14 14" aria-hidden="true">
          <circle cx="7" cy="7" r="6" fill="var(--accent)"/>
          <path d="M1 7 H13 M7 1 Q3.5 7 7 13 M7 1 Q10.5 7 7 13" fill="none" stroke="var(--card-grey)" stroke-width="1"/>
        </svg>
        www.quilmora.com
      </li>
    </ul>
  </section>
</body>
</html>
```